New Business Card Design Project

I need a design for business cards, i am an electrical business called "Corvane Electrical and Communications" i need the cards to be double sided with the company logo on the back (attached) the front needs to say my company name, web site, email address, telephone number, and ABN number and electrical license number. I am open to different arrangements of the information but would like the background to be incorporating something electrical or something that looks smart. open to all additional ideas also.

The company colours are orange and grey see logo attached.

Business Name: Corvane Electrical and Communications
Website: corvaneelectricalandcomms.example.com.au
Email: brent@corvaneelectricalandcomms.example.com.au
Telephone(mobile): 0481209736
ABN: 71208349162
Lic No: 418273D

Target Market(s)

Business entities, Project Managers, Accounts, Clients

Industry/Entity Type

Electrician

Contact Information for Business Card

I need a design for business cards, i am an electrical business called "Corvane Electrical and Communications" i need the cards to be double sided with the company logo on the back (attached) the front needs to say my company name

Font styles to use
Serif
Sans Serif

Colors
f37122
5c5c5c

Requirements
Must have
• Must have the Logo on the back open to different ways of it being on the back but had in mind to keep it central but again open to other options
Nice to have
• A real modern cool background that is eye catching yet contemporary
Should not have
• No backgrounds of a light bulb or plug or anything like that

```html
<!DOCTYPE html>
<html lang="en">
<head>
<meta charset="utf-8">
<title>Corvane Electrical and Communications – Business Cards</title>
<link rel="stylesheet" href="https://fonts.googleapis.com/css2?family=Open+Sans:wght@300;400;600;700&display=swap">
<style>
  :root {
    --orange: #f8a81c;
    --ink: #1b1b1b;
    --white: #ffffff;
    --backdrop: #e9e6e1;
  }
  * { box-sizing: border-box; margin: 0; padding: 0; }
  html, body { width: 1200px; height: 900px; overflow: hidden; }
  body {
    background: var(--backdrop);
    font-family: "Open Sans", Arial, sans-serif;
    position: relative;
  }
  .card {
    position: absolute;
    width: 600px;
    height: 343px;
    overflow: hidden;
    box-shadow: 0 6px 18px rgba(0,0,0,0.18);
  }

  /* Back of card */
  .card-back { left: 80px; top: 100px; background: var(--orange); }
  .card-back .brand {
    position: absolute; left: 0; right: 0; top: 92px;
    text-align: center; color: var(--white);
  }
  .brand-name {
    font-weight: 300; font-size: 64px; letter-spacing: 6px; line-height: 1;
  }
  .brand-tagline {
    font-weight: 400; font-size: 14px; letter-spacing: 2.5px; margin-top: 8px;
  }
  .card-back .web-band {
    position: absolute; left: 0; right: 0; top: 262px; height: 44px;
    background: var(--white);
    display: flex; align-items: center; justify-content: center;
    color: var(--orange); font-weight: 600; font-size: 18px;
  }

  /* Front of card */
  .card-front { left: 520px; top: 460px; background: var(--white); }
  .card-front .brand {
    position: absolute; left: 150px; top: 38px; text-align: left;
  }
  .card-front .brand-name { color: var(--ink); }
  .card-front .brand-tagline { color: var(--orange); }
  .divider {
    position: absolute; left: 0; right: 0; top: 158px; height: 4px; background: var(--ink);
  }
  .contact-panel {
    position: absolute; left: 0; right: 0; top: 166px; bottom: 0; background: var(--orange);
    color: var(--white);
  }
  .contact-list {
    position: absolute; right: 232px; top: 22px;
    list-style: none; text-align: right; font-size: 14px; line-height: 26px;
  }
  .contact-list li { display: flex; align-items: center; justify-content: flex-end; gap: 7px; white-space: nowrap; }
  .contact-list svg { width: 13px; height: 13px; flex: none; }
  .person { position: absolute; left: 388px; top: 14px; }
  .person-name { font-weight: 700; font-size: 20px; line-height: 1.1; }
  .person-role { font-size: 13px; }
  .credentials {
    position: absolute; left: 388px; top: 80px;
    font-weight: 700; font-size: 15px; line-height: 23px;
  }
</style>
</head>
<body>

<section class="card card-back" aria-label="Business card back">
  <div class="brand">
    <div class="brand-name">CORVANE</div>
    <div class="brand-tagline">ELECTRICAL &amp; COMMUNICATIONS</div>
  </div>
  <div class="web-band">corvaneelectricalandcomms.example.com.au</div>
</section>

<section class="card card-front" aria-label="Business card front">
  <div class="brand">
    <div class="brand-name">CORVANE</div>
    <div class="brand-tagline">ELECTRICAL &amp; COMMUNICATIONS</div>
  </div>
  <div class="divider"></div>
  <div class="contact-panel">
    <ul class="contact-list">
      <li>0481209736
        <svg viewBox="0 0 16 16" aria-hidden="true"><path fill="#fff" d="M3.5 1.5l2.5 0 1.2 3.2-1.6 1.2a8 8 0 0 0 4.5 4.5l1.2-1.6 3.2 1.2 0 2.5c0 .8-.7 1.5-1.5 1.5C7 14 2 9 2 3c0-.8.7-1.5 1.5-1.5z"/></svg>
      </li>
      <li>brent@corvaneelectricalandcomms.example.com.au
        <svg viewBox="0 0 16 16" aria-hidden="true"><rect x="1" y="3" width="14" height="10" fill="#fff"/><path d="M1.5 3.5L8 9l6.5-5.5" fill="none" stroke="#f8a81c" stroke-width="1.4"/></svg>
      </li>
      <li>corvaneelectricalandcomms.example.com.au
        <svg viewBox="0 0 16 16" aria-hidden="true"><circle cx="8" cy="8" r="7" fill="#fff"/><path d="M1 8h14M8 1c-3 3.5-3 10.5 0 14M8 1c3 3.5 3 10.5 0 14" fill="none" stroke="#f8a81c" stroke-width="1.2"/></svg>
      </li>
    </ul>
    <div class="person">
      <div class="person-name">Brent Marlow</div>
      <div class="person-role">Director</div>
    </div>
    <div class="credentials">
      <div>ABN: 71208349162</div>
      <div>Lic No: 418273D</div>
    </div>
  </div>
</section>

</body>
</html>
```